Modern business card design for professional copywriter

I'd like a business card design that I can use to have my cards printed out by quillprint.com as a squared corners business card (see artwork and design guidelines here: https://help.quillprint.com/hc/en-gb/sections/200570950-QUILL-Product-Templates)

The design should be clean and modern and reflect the colours, tone and branding on my website: https://tessavorrin.com.au

Target Market(s)

Professionals, B2B small business owners

Industry/Entity Type

Business

Contact Information for Business Card

Tessa Vorrin
m: 0468 905 327
e: tessa@tessavorrin.com.au
w: tessavorrin.com.au

Font styles to use
Sans Serif

Requirements
Must have
• Tagline: "Smart copywriting for clever business people"
• Brand colours: fd8000, 009984, 666666 and black
Nice to have

```html
<!DOCTYPE html>
<html lang="en">
<head>
<meta charset="utf-8">
<title>Tessa Vorrin – Copywriter business card</title>
<link rel="stylesheet" href="https://fonts.googleapis.com/css2?family=Lato:ital,wght@0,400;0,700;0,900;1,700&family=Tinos:ital,wght@1,700&display=swap">
<style>
  :root {
    --teal: #009984;
    --teal-light: #35a58f;
    --teal-dark: #2a8f79;
    --orange: #fd8000;
    --grey: #666666;
    --ink: #111111;
    --paper: #ffffff;
    --backdrop: #ececec;
  }
  * { box-sizing: border-box; margin: 0; padding: 0; }
  html, body { width: 1200px; height: 586px; overflow: hidden; }
  body {
    background: var(--backdrop);
    font-family: "Lato", sans-serif;
    position: relative;
  }
  .card {
    position: absolute;
    top: 143px;
    width: 500px;
    height: 300px;
    overflow: hidden;
  }
  .card--front { left: 62px; }
  .card--back { left: 619px; background: var(--paper); }

  .front-pattern {
    position: absolute; inset: 0;
    background: linear-gradient(135deg, var(--teal-light) 0%, var(--teal-dark) 55%, var(--teal-light) 100%);
  }
  .front-brand {
    position: absolute;
    left: 0; right: 0; top: 118px;
    text-align: center;
    color: var(--paper);
  }
  .front-brand .brand-name { font-size: 50px; font-weight: 400; line-height: 1; letter-spacing: -0.5px; }
  .front-brand .brand-role { font-size: 15px; letter-spacing: 7px; margin-top: 4px; padding-left: 120px; }

  .back-brand {
    position: absolute; left: 0; right: 0; top: 42px;
    text-align: center;
  }
  .back-brand .brand-name { font-size: 36px; font-weight: 400; color: var(--teal); line-height: 1; }
  .back-brand .brand-role { font-size: 11px; letter-spacing: 5px; color: var(--grey); margin-top: 3px; padding-left: 90px; }

  .services {
    position: absolute; right: 290px; top: 133px;
    list-style: none; text-align: right;
    font-size: 11px; font-weight: 700; color: var(--ink);
    line-height: 18.5px;
  }
  .divider {
    position: absolute; left: 228px; top: 128px; width: 5px; height: 122px;
    background: radial-gradient(circle, var(--orange) 2.2px, transparent 2.6px) 0 0 / 5px 9.3px repeat-y;
  }
  .contact { position: absolute; left: 251px; top: 146px; }
  .social { display: flex; gap: 8px; margin-bottom: 9px; }
  .social span { width: 19px; height: 19px; border-radius: 50%; background: var(--orange); }
  .contact-row { display: flex; align-items: center; gap: 7px; font-size: 12px; color: var(--ink); height: 24px; }
  .contact-row svg { width: 17px; height: 17px; }
  .contact-web { font-size: 12px; font-weight: 900; color: var(--teal); letter-spacing: 0.8px; margin-top: 3px; }

  .band-teal { position: absolute; left: 0; right: 0; top: 274px; height: 5px; background: var(--teal); }
  .band-orange {
    position: absolute; left: 0; right: 0; top: 279px; height: 21px;
    background: var(--orange);
    font-family: "Tinos", serif; font-style: italic; font-weight: 700;
    font-size: 12px; color: var(--ink); text-align: center; line-height: 21px;
  }
</style>
</head>
<body>
  <section class="card card--front">
    <div class="front-pattern" role="img" aria-label="Faceted teal low-poly background pattern"></div>
    <div class="front-brand">
      <div class="brand-name">Tessa Vorrin</div>
      <div class="brand-role">COPYWRITER</div>
    </div>
  </section>

  <section class="card card--back">
    <div class="back-brand">
      <div class="brand-name">Tessa Vorrin</div>
      <div class="brand-role">COPYWRITER</div>
    </div>

    <ul class="services">
      <li>Feature Writing</li>
      <li>SEO Copywriting</li>
      <li>Legal Copywriting</li>
      <li>Content Marketing</li>
      <li>Website Copywriting</li>
      <li>Small Business Copywriting</li>
    </ul>

    <div class="divider"></div>

    <div class="contact">
      <div class="social" role="img" aria-label="Social network links">
        <span></span><span></span><span></span><span></span>
      </div>
      <div class="contact-row">
        <svg viewBox="0 0 20 20" aria-hidden="true">
          <circle cx="10" cy="10" r="10" fill="#009984"/>
          <path d="M5 8.5c0-1.5 2.2-2.5 5-2.5s5 1 5 2.5v1h-2.5v-1.2h-5v1.2H5z M6.5 10.5h7l1 4h-9z" fill="#fff"/>
        </svg>
        <span>0468 905 327</span>
      </div>
      <div class="contact-row">
        <svg viewBox="0 0 20 20" aria-hidden="true">
          <circle cx="10" cy="10" r="10" fill="#009984"/>
          <rect x="5" y="6.5" width="10" height="7" fill="none" stroke="#fff" stroke-width="1.3"/>
          <path d="M5 6.5l5 4 5-4" fill="none" stroke="#fff" stroke-width="1.3"/>
        </svg>
        <span>tessa@tessavorrin.com.au</span>
      </div>
      <div class="contact-web">www.tessavorrin.com.au</div>
    </div>

    <div class="band-teal"></div>
    <div class="band-orange">Smart copywriting for clever business people</div>
  </section>
</body>
</html>
```